Buch-/eBook-Cover für Traumatherapeutin
Zielgruppe
Ich bin Traumatherapeutin und schreibe ein Buch zum Thema Trauma bearbeiten.
Meine Zielgruppe sucht Heilung, Genesung, Selbstliebe etc.
Aufgabenstellung
Buchcover
Bitte erstell mir ein modernes positives inspirierendes Buchcover mit dem
Titel: 'Morgenlicht NEU entdecken“
Untertitel: „Spüre den Mut der ganz in dir wohnt“
Dr. Mira Kessow
Ich hätte gerne ein modernes Buch, das entweder einen Bezug zum Thema Trauma hat oder aber einfach stylische Schriftzüge. Bin aber auch offen für andere Vorschläge.
Dunkelblau, weiß und türkis oder auch rosa mag ich ganz gerne. Wobei Dunkelblau, weiß und türkis meine Favoriten sind und mit rosa höchstens kleinere Akzente gesetzt werden sollten.
Das Buchcover soll modern sein und direkt ansprechen. Gerne eine originelle Lösung, oder etwas Besonderes, etwas das Tiefe ausdrückt, oder man mehrmals hinsehen muss um etwas zu erkennen oder etwas das mehr Interpretationsspielraum lässt.
Gerne auch viel weiß, zumindest heller und nicht zu dunkel. Stylish, aber nicht überfrachtet.
Schreib mich gerne an, wenn du Fragen hast.
Ich habe mal zwei Beispiel von Typolösungen angehängt, die ich ganz cool fände.
Ich freue mich auf deine Ideen :-)
Ganz liebe Grüße
Mira

```html
<!DOCTYPE html>
<html lang="de">
<head>
<meta charset="utf-8">
<title>Morgenlicht neu entdecken – Buchcover</title>
<link rel="stylesheet" href="https://fonts.googleapis.com/css2?family=Bebas+Neue&family=Roboto:wght@400&family=Yellowtail&display=swap">
<style>
  :root {
    --paper: #ffffff;
    --teal: #50b8a6;
    --gold-light: #d3c143;
    --gold-dark: #a68c1a;
    --boat-wood: #e2b46a;
    --boat-hull: #2c4a7a;
  }
  html, body {
    margin: 0;
    padding: 0;
    overflow: hidden;
    background: var(--paper);
  }
  .cover {
    position: relative;
    width: 750px;
    height: 1200px;
    background: var(--paper);
    overflow: hidden;
  }
  .cover-type {
    position: absolute;
    inset: 0;
    width: 750px;
    height: 1200px;
  }
  .author {
    font-family: "Bebas Neue", "Arial Narrow", sans-serif;
    font-size: 38px;
    fill: var(--teal);
  }
  .title-block {
    font-family: "Bebas Neue", "Arial Narrow", sans-serif;
    font-size: 172px;
    fill: var(--teal);
  }
  .title-script {
    font-family: "Yellowtail", cursive;
    font-size: 230px;
    fill: url(#goldBrush);
  }
  .subtitle {
    font-family: "Roboto", Arial, sans-serif;
    font-size: 35px;
    fill: var(--teal);
  }
  .boat-illustration {
    position: absolute;
    left: 300px;
    top: 915px;
    width: 135px;
    height: 95px;
    border-radius: 40% 40% 45% 45%;
    background: radial-gradient(ellipse at 55% 45%, var(--boat-wood) 0%, #e9d2a4 45%, rgba(44, 74, 122, 0.35) 80%, rgba(255,255,255,0) 100%);
    transform: rotate(18deg);
  }
</style>
</head>
<body>
  <main class="cover">
    <svg class="cover-type" viewBox="0 0 750 1200" xmlns="http://www.w3.org/2000/svg">
      <defs>
        <linearGradient id="goldBrush" x1="0" y1="0" x2="1" y2="0.3">
          <stop offset="0" stop-color="var(--gold-light)"/>
          <stop offset="0.45" stop-color="var(--gold-dark)"/>
          <stop offset="0.7" stop-color="var(--gold-light)"/>
          <stop offset="1" stop-color="var(--gold-light)"/>
        </linearGradient>
      </defs>

      <text class="author" x="375" y="106" text-anchor="middle">Dr. Mira Kessow</text>

      <text class="title-block" x="375" y="270" text-anchor="middle" textLength="660" lengthAdjust="spacingAndGlyphs">MORGENLICHT</text>
      <text class="title-block" x="375" y="580" text-anchor="middle" textLength="640" lengthAdjust="spacingAndGlyphs">ENTDECKEN</text>
      <text class="title-script" x="380" y="430" text-anchor="middle">neu</text>

      <text class="subtitle" x="375" y="640" text-anchor="middle">Spüre den Mut der ganz in dir wohnt</text>
    </svg>

    <div class="boat-illustration" role="img" aria-label="Kleines hölzernes Ruderboot mit Rudern, von oben gesehen"></div>
  </main>
</body>
</html>
```